Real Estate stationery - need an interesting, eye catching design

I need a letterhead and #10 envelope design in the same theme.
I am looking for an interesting, eye catching design that would stand out in the crowd. I am in the real estate business(which is very competitive) in Florida so standing out and being different is very important to me.
Marguerite(Rita) Delacourt (name), RealtorĀ® (title), 352-608-2147 (cell), bayviewritahomes@quellmail.com (email), www.bayviewritahomes.com(website), 915 Calloway Creek Blvd.,Ste. 3140, Marlow Springs, FL 34127 (business address)

```html
<!DOCTYPE html>
<html lang="en">
<head>
<meta charset="utf-8">
<title>Harborline Realty Stationery</title>
<link href="https://fonts.googleapis.com/css2?family=Raleway:wght@300;400;500&family=Roboto:wght@400&display=swap" rel="stylesheet">
<style>
  :root {
    --backdrop: #dedede;
    --paper: #f7f7f7;
    --paper-edge: #ffffff;
    --brand-brown: #7d5725;
    --text-dark: #3a3a3a;
    --text-body: #6b6b6b;
    --on-brown: #ffffff;
    --signature-tone: #d9ccb8;
  }
  * { margin: 0; padding: 0; box-sizing: border-box; }
  html, body { width: 1200px; height: 843px; overflow: hidden; background: var(--backdrop); }
  body { position: relative; font-family: "Raleway", sans-serif; }

  .sheet {
    position: absolute;
    background: linear-gradient(90deg, var(--paper-edge), var(--paper));
    box-shadow: 0 6px 14px rgba(0,0,0,0.18);
    overflow: hidden;
  }
  .band { position: absolute; left: 0; bottom: 0; display: block; }

  .brand-name {
    font-family: "Raleway", sans-serif;
    font-weight: 500;
    color: var(--brand-brown);
    letter-spacing: 0.5px;
    display: flex; align-items: center; gap: 6px;
    white-space: nowrap;
  }
  .brand-name .brand-dot { width: 8px; height: 8px; background: currentColor; }

  /* Letterhead */
  .letterhead { left: 74px; top: 61px; width: 508px; height: 716px; }
  .letterhead .brand-name { position: absolute; top: 86px; left: 0; width: 100%; justify-content: center; font-size: 18px; }
  .salutation { position: absolute; left: 44px; top: 199px; font-size: 13px; font-weight: 400; color: var(--text-dark); }
  .letter-body { position: absolute; left: 44px; top: 238px; width: 422px; font-size: 7.4px; line-height: 11px; color: var(--text-body); text-align: justify; font-weight: 400; letter-spacing: 0.15px; }
  .letter-body p { margin-bottom: 11px; }
  .closing { position: absolute; left: 44px; top: 471px; font-size: 7px; color: var(--text-body); }
  .signature { position: absolute; left: 40px; top: 498px; width: 90px; height: 36px; background: var(--signature-tone); border-radius: 4px; }

  .contact-list { position: absolute; left: 37px; top: 669px; list-style: none; font-family: "Roboto", sans-serif; font-size: 7.4px; line-height: 9.3px; color: var(--on-brown); }
  .contact-list li { display: flex; align-items: center; gap: 5px; }
  .contact-list svg { width: 6px; height: 6px; flex: none; }
  .address { position: absolute; font-family: "Roboto", sans-serif; font-size: 7.4px; line-height: 9.3px; color: var(--on-brown); font-style: normal; white-space: nowrap; }
  .letterhead .address { right: 31px; top: 671px; text-align: right; }

  /* Envelope back */
  .envelope-back { left: 621px; top: 275px; width: 512px; height: 233px; }
  .envelope-back .flap { position: absolute; left: 0; top: 0; display: block; }
  .envelope-back .brand-name { position: absolute; top: 29px; left: 0; width: 100%; justify-content: center; font-size: 13px; color: var(--on-brown); }

  /* Envelope front */
  .envelope-front { left: 621px; top: 543px; width: 512px; height: 233px; }
  .envelope-front .brand-name { position: absolute; left: 24px; top: 40px; font-size: 14px; }
  .envelope-front .address { left: 27px; top: 186px; }
</style>
</head>
<body>

  <section class="sheet letterhead" aria-label="Letterhead">
    <div class="brand-name"><span class="brand-dot"></span>Harborline Realty</div>

    <p class="salutation">Dear Mr. Hale,</p>

    <div class="letter-body">
      <p>Lorem ipsum dolor sit amet, consectetur adipiscing elit. Donec orci purus, luctus vitae dignissim eu, iaculis sed purus. Vivamus faucibus, ipsum nec aliquet viverra, leo mauris condimentum ligula, sit amet sagittis enim ligula quis arcu. Nam egestas tortor id nisi porttitor mattis. In tortor ante, ultricies in suscipit a, tempus non massa. Vivamus et auctor mi. Fusce vel massa nulla. Phasellus nec eros mauris, et scelerisque orci.</p>
      <p>Donec malesuada orci vitae nulla accumsan porta a id massa. Quisque accumsan iaculis magna sit amet fringilla. Maecenas consequat, magna eget tincidunt semper, odio nibh rutrum mi, id feugiat ante nisi eu risus. Vestibulum nunc orci, rhoncus a placerat in, ultricies in mi. Cras mattis varius eros, vel fringilla nisi suscipit eget. Quisque scelerisque sagittis nulla at porttitor.</p>
      <p>Sed id augue vitae urna euismod commodo aliquet a quam. Pellentesque arcu velit, cursus et malesuada ut, consequat et diam. Nullam erat sem, rhoncus id ullamcorper vitae, rhoncus et arcu. In ultricies ultricies nulla, ut rutrum nisi iaculis at. Donec eu magna a metus ornare faucibus. Fusce aliquet faucibus ultricies. Morbi semper, est id tincidunt gravida, sem arcu adipiscing lacus, ac bibendum nulla leo eu purus. Quisque nec diam sed risus consectetur a accumsan quis quis nibh. Vestibulum id purus lorem.</p>
      <p>It is a long established fact that a reader will be distracted by the readable content of a page when looking at its layout. The point of using Lorem Ipsum is that it has a more-or-less normal distribution of letters, as opposed to using 'Content here, content here', making it look like readable English. Many desktop publishing packages</p>
    </div>

    <p class="closing">Sincerely,</p>
    <div class="signature" role="img" aria-label="Handwritten signature of Marguerite Delacourt"></div>

    <svg class="band" width="508" height="716" viewBox="0 0 508 716" aria-hidden="true">
      <polygon points="0,625 254,705 508,625 508,716 0,716" fill="var(--brand-brown)"/>
    </svg>

    <ul class="contact-list">
      <li><svg viewBox="0 0 6 6"><rect x="1.2" y="0" width="3.6" height="6" rx="0.6" fill="#fff"/><rect x="1.8" y="0.8" width="2.4" height="3.6" fill="var(--brand-brown)"/></svg>352-608-2147</li>
      <li><svg viewBox="0 0 6 6"><rect x="0" y="1" width="6" height="4" fill="#fff"/><polyline points="0,1 3,3.4 6,1" fill="none" stroke="var(--brand-brown)" stroke-width="0.6"/></svg>bayviewritahomes@quellmail.com</li>
      <li><svg viewBox="0 0 6 6"><circle cx="3" cy="3" r="3" fill="#fff"/><ellipse cx="3" cy="3" rx="1.2" ry="3" fill="none" stroke="var(--brand-brown)" stroke-width="0.5"/><line x1="0" y1="3" x2="6" y2="3" stroke="var(--brand-brown)" stroke-width="0.5"/></svg>www.bayviewritahomes.com</li>
    </ul>
    <address class="address">915 Calloway Creek Blvd.<br>Ste. 3140<br>Marlow Springs, FL 34127</address>
  </section>

  <section class="sheet envelope-back" aria-label="Envelope back">
    <svg class="flap" width="512" height="72" viewBox="0 0 512 72" aria-hidden="true">
      <path d="M0,0 H512 V0 C505,30 500,72 470,72 H42 C12,72 7,30 0,0 Z" fill="var(--brand-brown)"/>
    </svg>
    <div class="brand-name"><span class="brand-dot"></span>Harborline Realty</div>
  </section>

  <section class="sheet envelope-front" aria-label="Envelope front">
    <div class="brand-name"><span class="brand-dot"></span>Harborline Realty</div>
    <svg class="band" width="512" height="233" viewBox="0 0 512 233" aria-hidden="true">
      <polygon points="0,143 256,224 512,143 512,233 0,233" fill="var(--brand-brown)"/>
    </svg>
    <address class="address">915 Calloway Creek Blvd.<br>Ste. 3140<br>Marlow Springs, FL 34127</address>
  </section>

</body>
</html>
```